Alapca breeding needs a website

Presentation of the farm, animals (stallions, mares, information about the animals, for sale) and possible later expansion with a webshop (alpaca wool products). We want to present our farm and the animals on the farm on this page. A mission why we are doing this. Furthermore, each animal should be shown with a picture and described. Later we want to sell our own products made from alpaca wool via a webshop. But we still need to grow a bit to do that.

Target Market(s)

Information about my alpaca breeding and the alpaca farm

Industry/Entity Type

Tierzucht

Number of Pages Required

1 page

Font styles to use
Sans Serif

Requirements
Must have
• Modern design that matches the logo
Nice to have
• Intuitive operation / Clear structure
Should not have
• No

```html
<!DOCTYPE html>
<html lang="en">
<head>
<meta charset="utf-8">
<title>Meadowrun Alpacas</title>
<link href="https://fonts.googleapis.com/css2?family=Cinzel:wght@700&family=Roboto:wght@400;500;700&display=swap" rel="stylesheet">
<style>
:root{
  --navy:#0d2b55;
  --navy-deep:#0a2348;
  --green:#7cc242;
  --green-dark:#6aad34;
  --mint:#eef8e1;
  --text:#6b6b6b;
  --white:#ffffff;
}
*{margin:0;padding:0;box-sizing:border-box}
html,body{width:1200px;height:3375px;overflow:hidden}
body{position:relative;background:var(--white);font-family:'Roboto',sans-serif;color:var(--text)}
.abs{position:absolute}
.display{font-family:'Cinzel',serif;font-weight:700;letter-spacing:1px}
.btn{position:absolute;display:flex;align-items:center;justify-content:center;gap:10px;background:var(--green);color:var(--white);font-weight:700;font-size:16px;border-radius:30px;text-transform:uppercase;letter-spacing:.2px}
.btn .go{width:20px;height:20px;border-radius:50%;background:var(--white);display:flex;align-items:center;justify-content:center}

/* header */
.header{position:absolute;left:0;top:0;width:1200px;height:107px;background:var(--white);z-index:3}
.brand-disc{position:absolute;left:132px;top:-40px;width:238px;height:236px;border-radius:50%;background:var(--white);z-index:4;display:flex;align-items:flex-end;justify-content:center;padding-bottom:48px}
.brand-name{font-family:'Cinzel',serif;font-weight:700;font-size:27px;color:var(--navy);text-align:center;line-height:1.05}
.topbar{position:absolute;left:582px;top:0;width:474px;height:42px;background:var(--navy);border-radius:0 0 22px 22px;display:flex;align-items:center;padding:0 12px 0 30px;gap:10px}
.topbar .call{color:var(--green);font-weight:700;font-size:16px}
.topbar .call b{color:var(--white)}
.search{margin-left:auto;width:140px;height:30px;border-radius:15px;background:var(--white);display:flex;align-items:center;justify-content:space-between;padding:0 4px 0 14px;font-size:11px;color:#444}
.search i{width:22px;height:22px;border-radius:50%;background:var(--green);display:flex;align-items:center;justify-content:center}
.nav{position:absolute;top:70px;font-size:13px;font-weight:700;color:#222;z-index:4}

/* hero */
.hero{position:absolute;left:0;top:107px;width:1200px;height:600px;background:linear-gradient(180deg,#6b6a48 0%,#8a7a45 35%,#6d6a36 60%,#4d4a2a 100%)}
.hero-title{position:absolute;top:252px;width:1200px;text-align:center;font-size:66px;color:var(--white);font-family:'Cinzel',serif;font-weight:700}
.hero-sub{position:absolute;top:347px;width:1200px;text-align:center;font-size:18px;font-weight:500;color:var(--white)}
.dots span{position:absolute;left:1126px;width:8px;height:8px;border-radius:50%;background:var(--white)}

/* sections */
.h2{position:absolute;font-size:52px;color:var(--navy);font-family:'Cinzel',serif;font-weight:700;white-space:nowrap}
.h2 em{font-style:normal;color:var(--green)}
.para{position:absolute;font-size:15.5px;line-height:26px;text-align:justify}
.photo{position:absolute;border-radius:50%}
.ring{position:absolute;border-radius:50%;border:4px solid var(--green);background:var(--white);overflow:hidden}
.ring .pic{position:absolute;left:16px;top:16px;width:262px;height:262px;border-radius:50%;overflow:hidden}
.ring .tag{position:absolute;left:0;right:0;bottom:0;height:80px;border-radius:130px 130px 0 0;display:flex;align-items:center;justify-content:center;color:var(--white);font-weight:700;font-size:16px}
.arrow{position:absolute}
.prod{position:absolute;width:264px;height:264px;border-radius:50%;border:2px solid #b7b7b7;background:var(--white);overflow:hidden}
.prod .cart{position:absolute;left:111px;top:111px;width:42px;height:42px;border-radius:50%;background:var(--green);display:flex;align-items:center;justify-content:center}
.pname{position:absolute;width:264px;text-align:center;font-size:19px;font-weight:500;color:#333}
.price{position:absolute;width:264px;text-align:center;font-size:19px;font-weight:500;color:var(--green)}
.stars{position:absolute;width:264px;text-align:center;font-size:13px;color:#f2c200;letter-spacing:5px}

/* footer */
.fhead{position:absolute;font-size:18px;font-weight:700;color:var(--white)}
.ftext{position:absolute;font-size:13px;line-height:21px;color:var(--white)}
.fdiv{position:absolute;top:3010px;width:1px;height:200px;background:rgba(255,255,255,.2)}
.social{position:absolute;top:3312px;width:30px;height:30px;border-radius:50%;border:1.5px solid var(--white)}
</style>
</head>
<body>

<!-- hero -->
<div class="hero" role="img" aria-label="Farm pasture at sunset with wooden fences and grazing alpacas"></div>
<div class="hero-title">MEADOWRUN ALPACAS</div>
<div class="hero-sub">EXCEPTEUR SINT OCCAECAT CUPIDATA</div>
<div class="btn" style="left:524px;top:409px;width:152px;height:53px">GET STARTED <span class="go"><svg width="10" height="10" viewBox="0 0 10 10"><path d="M3 1l4 4-4 4" stroke="#7cc242" stroke-width="2" fill="none"/></svg></span></div>
<div class="dots"><span style="top:510px"></span><span style="top:526px;background:var(--green)"></span><span style="top:542px"></span></div>

<svg class="abs" style="left:0;top:560px" width="1200" height="170" viewBox="0 560 1200 170">
  <path d="M140 670 C 380 610, 650 560, 850 576 C 1000 590, 1110 630, 1160 668" stroke="var(--navy)" stroke-width="10" fill="none"/>
  <path d="M0 702 C 250 672, 600 580, 860 590 C 1010 598, 1130 650, 1200 700 L1200 730 L0 730 Z" fill="var(--white)"/>
</svg>

<!-- header -->
<header class="header"></header>
<div class="brand-disc"><div class="brand-name">MEADOWRUN<br>ALPACAS</div></div>
<div class="topbar" style="z-index:4">
  <svg width="22" height="22" viewBox="0 0 22 22"><circle cx="11" cy="11" r="11" fill="var(--green)"/><path d="M7 5.5l2.5 0 1 3-1.5 1.2c.8 1.6 2 2.8 3.6 3.6l1.2-1.5 3 1v2.5c0 .6-.5 1-1 1C10 16.3 5.7 12 5.7 6.5c0-.5.5-1 1.3-1z" fill="var(--white)"/></svg>
  <span class="call">CALL US : <b>+1 555 010 0199</b></span>
  <div class="search">Search Products <i><svg width="11" height="11" viewBox="0 0 11 11"><circle cx="4.5" cy="4.5" r="3.3" stroke="#fff" stroke-width="1.6" fill="none"/><path d="M7 7l3 3" stroke="#fff" stroke-width="1.6"/></svg></i></div>
</div>
<nav>
  <span class="nav" style="left:575px">HOME</span>
  <span class="nav" style="left:653px">ABOUT</span>
  <span class="nav" style="left:736px">MISSION</span>
  <span class="nav" style="left:831px">WEBSHOP</span>
  <span class="nav" style="left:935px">CONTACT</span>
  <svg class="abs" style="left:1024px;top:62px;z-index:4" width="30" height="28" viewBox="0 0 30 28"><path d="M2 4h4l3 14h14l3-10H8" stroke="#222" stroke-width="2" fill="none"/><circle cx="11" cy="23" r="2" fill="#222"/><circle cx="21" cy="23" r="2" fill="#222"/><circle cx="25" cy="4" r="4" fill="var(--green)"/></svg>
</nav>

<!-- about -->
<div class="photo" role="img" aria-label="White alpaca standing at a farm fence" style="left:170px;top:673px;width:294px;height:294px;background:linear-gradient(160deg,#8b7b66,#c9c2b3 45%,#5f5a4c)"></div>
<div class="photo" style="left:321px;top:862px;width:220px;height:220px;background:var(--white)"></div>
<div class="photo" role="img" aria-label="Group of alpacas grazing on a green meadow" style="left:331px;top:872px;width:200px;height:200px;background:linear-gradient(180deg,#6b8f3c,#7fb23e 50%,#5d9a2c)"></div>
<h2 class="h2" style="left:586px;top:686px">ABOUT <em>US</em></h2>
<p class="para" style="left:586px;top:763px;width:469px">Sed ut perspiciatis unde omnis iste natus error sit voluptatem accusantium doloremque laudantium, totam rem aperiam, eaque ipsa quae ab illo inventore veritatis et quasi architecto beatae vitae dicta sunt explicabo. Nemo enim ipsam voluptatem quia voluptas sit aspernatur aut odit aut fugit, sed quia consequuntur magni dolores eos qui ratione voluptatem sequi nesciunt. Neque porro quisquam est, qui dolorem ipsum quia dolor sit amet, consectetur, adipisci velit, sed quia non ni tebore et dmagnam aliquam quaerat voluptatem</p>
<div class="btn" style="left:586px;top:1000px;width:153px;height:53px">READ MORE <span class="go"><svg width="10" height="10" viewBox="0 0 10 10"><path d="M3 1l4 4-4 4" stroke="#7cc242" stroke-width="2" fill="none"/></svg></span></div>

<!-- mission -->
<svg class="abs" style="left:0;top:1120px" width="1200" height="450" viewBox="0 1120 1200 450">
  <path d="M0 1380 C 60 1250, 230 1150, 430 1140 L 900 1134 C 1050 1140, 1150 1170, 1200 1205 L 1200 1468 C 1050 1458, 820 1462, 600 1492 C 400 1522, 200 1585, 0 1518 Z" fill="var(--navy)"/>
</svg>
<h2 class="h2" style="left:144px;top:1242px;line-height:56px;color:var(--white)">OUR<br><em>MISSION</em></h2>
<p class="para" style="left:443px;top:1248px;width:612px;color:var(--white);font-size:15.5px">Sed ut perspiciatis unde omnis iste natus error sit voluptatem accusantium doloremque laudantium, totam rem aperiam, eaque ipsa quae ab illo inventore veritatis et quasi architecto beatae vitae dicta sunt explicabo. Nemo enim ipsam voluptatem quia voluptas sit aspernatur aut odit aut fugit, sed quia consequuntur magni dolores eos qui ratione</p>
<div class="btn" style="left:443px;top:1379px;width:153px;height:54px">READ MORE <span class="go"><svg width="10" height="10" viewBox="0 0 10 10"><path d="M3 1l4 4-4 4" stroke="#7cc242" stroke-width="2" fill="none"/></svg></span></div>

<!-- animals -->
<h2 class="h2" style="left:0;width:1200px;text-align:center;top:1604px">OUR <em>ANIMALS</em></h2>
<svg class="arrow" style="left:88px;top:1820px" width="32" height="64" viewBox="0 0 32 64"><path d="M30 2L2 32l28 30" stroke="#9a9a9a" stroke-width="1.5" fill="none"/></svg>
<svg class="arrow" style="left:1080px;top:1820px" width="32" height="64" viewBox="0 0 32 64"><path d="M2 2l28 30L2 62" stroke="#9a9a9a" stroke-width="1.5" fill="none"/></svg>

<div class="ring" style="left:146px;top:1703px;width:298px;height:298px">
  <div class="pic" role="img" aria-label="Brown stallion walking in a paddock" style="background:linear-gradient(180deg,#e6ecef 0%,#5f8a4a 35%,#8b7a63 65%,#a08a70)"></div>
  <div class="tag" style="left:40px;right:40px;bottom:16px;background:var(--green)">STALLIONS</div>
</div>
<div class="ring" style="left:450px;top:1703px;width:298px;height:298px">
  <div class="pic" role="img" aria-label="Chestnut mare standing in a field" style="background:linear-gradient(180deg,#9db4d6 0%,#c3d2e3 45%,#b6c46a 75%,#8eaa44)"></div>
  <div class="tag" style="left:40px;right:40px;bottom:16px;background:var(--navy)">MARES</div>
</div>
<div class="ring" style="left:754px;top:1703px;width:298px;height:298px">
  <div class="pic" role="img" aria-label="Alpaca eating grass" style="background:linear-gradient(160deg,#6f8f46,#c9b79a 45%,#e8e2d6 60%,#7d9b4c)"></div>
  <div class="tag" style="left:40px;right:40px;bottom:16px;background:var(--green)">ALPACA</div>
</div>
<div class="btn" style="left:479px;top:2047px;width:240px;height:54px">VIEW MORE PRODUCTS <span class="go"><svg width="10" height="10" viewBox="0 0 10 10"><path d="M3 1l4 4-4 4" stroke="#7cc242" stroke-width="2" fill="none"/></svg></span></div>

<!-- shop -->
<div class="abs" style="left:0;top:2175px;width:1200px;height:800px;background:var(--mint)"></div>
<h2 class="h2" style="left:0;width:1200px;text-align:center;top:2255px">OUR <em>SHOP</em></h2>
<svg class="arrow" style="left:88px;top:2460px" width="32" height="64" viewBox="0 0 32 64"><path d="M30 2L2 32l28 30" stroke="#9a9a9a" stroke-width="1.5" fill="none"/></svg>
<svg class="arrow" style="left:1080px;top:2460px" width="32" height="64" viewBox="0 0 32 64"><path d="M2 2l28 30L2 62" stroke="#9a9a9a" stroke-width="1.5" fill="none"/></svg>

<div class="prod" style="left:144px;top:2360px">
  <div class="abs" role="img" aria-label="Felted alpaca wool balls in green and blue" style="left:14px;top:90px;width:232px;height:70px;border-radius:35px;background:linear-gradient(90deg,#8ccf3c,#b8c2b8 45%,#3dbad0)"></div>
  <div class="cart"><svg width="18" height="16" viewBox="0 0 18 16"><path d="M1 2h3l2 8h8l2-6H5" stroke="#fff" stroke-width="1.8" fill="none"/><circle cx="7" cy="13.5" r="1.3" fill="#fff"/><circle cx="13" cy="13.5" r="1.3" fill="#fff"/></svg></div>
</div>
<div class="prod" style="left:468px;top:2360px">
  <div class="abs" role="img" aria-label="Orange alpaca wool sweater" style="left:62px;top:50px;width:140px;height:160px;border-radius:30px 30px 12px 12px;background:linear-gradient(180deg,#f0a830,#e39420)"></div>
  <div class="cart"><svg width="18" height="16" viewBox="0 0 18 16"><path d="M1 2h3l2 8h8l2-6H5" stroke="#fff" stroke-width="1.8" fill="none"/><circle cx="7" cy="13.5" r="1.3" fill="#fff"/><circle cx="13" cy="13.5" r="1.3" fill="#fff"/></svg></div>
</div>
<div class="prod" style="left:790px;top:2360px">
  <div class="abs" role="img" aria-label="Light blue knitted alpaca wool beanie" style="left:62px;top:42px;width:140px;height:160px;border-radius:70px 70px 10px 10px;background:linear-gradient(180deg,#b5d3e6,#8fb6cf)"></div>
  <div class="cart"><svg width="18" height="16" viewBox="0 0 18 16"><path d="M1 2h3l2 8h8l2-6H5" stroke="#fff" stroke-width="1.8" fill="none"/><circle cx="7" cy="13.5" r="1.3" fill="#fff"/><circle cx="13" cy="13.5" r="1.3" fill="#fff"/></svg></div>
</div>

<div class="pname" style="left:145px;top:2642px">Product Name</div>
<div class="price" style="left:145px;top:2670px">$56.78</div>
<div class="stars" style="left:145px;top:2702px">★★★★★</div>
<div class="pname" style="left:469px;top:2642px">Product Name</div>
<div class="price" style="left:469px;top:2670px">$56.78</div>
<div class="stars" style="left:469px;top:2702px">★★★★★</div>
<div class="pname" style="left:791px;top:2642px">Product Name</div>
<div class="price" style="left:791px;top:2670px">$56.78</div>
<div class="stars" style="left:791px;top:2702px">★★★★★</div>

<div class="btn" style="left:479px;top:2758px;width:240px;height:53px">VIEW MORE PRODUCTS <span class="go"><svg width="10" height="10" viewBox="0 0 10 10"><path d="M3 1l4 4-4 4" stroke="#7cc242" stroke-width="2" fill="none"/></svg></span></div>

<div class="abs" role="img" aria-label="Mare and foal grazing on a grassy hillside" style="left:920px;top:2720px;width:250px;height:160px;border-radius:40% 60% 20% 20%;background:linear-gradient(160deg,#b5652a,#8a4a1e 60%,#a8c77a)"></div>

<!-- footer -->
<svg class="abs" style="left:0;top:2820px" width="1200" height="555" viewBox="0 2820 1200 555">
  <path d="M0 2828 C 200 2962, 500 2992, 800 2932 C 1000 2892, 1120 2862, 1200 2842 L1200 2900 C 1120 2900 1000 2935 800 2970 C 500 3010 200 2990 0 2900 Z" fill="#b2d98a"/>
  <path d="M0 2870 C 200 2990, 500 3010, 800 2960 C 1000 2925, 1120 2900, 1200 2885 L1200 3375 L0 3375 Z" fill="var(--navy-deep)"/>
</svg>

<div class="fhead" style="left:163px;top:3019px">CONTACT US</div>
<div class="fdiv" style="left:443px"></div>
<div class="fhead" style="left:523px;top:3019px">SIGN UP FOR NEWSLETTER</div>
<div class="fdiv" style="left:851px"></div>
<div class="fhead" style="left:921px;top:3019px">QUICK LINKS</div>

<svg class="abs" style="left:167px;top:3066px" width="16" height="22" viewBox="0 0 16 22"><path d="M8 0a8 8 0 0 0-8 8c0 6 8 14 8 14s8-8 8-14a8 8 0 0 0-8-8z" fill="#fff"/><circle cx="8" cy="8" r="3" fill="var(--navy-deep)"/></svg>
<div class="ftext" style="left:200px;top:3064px">1323,Excepteur sint occaecat<br>cupidatat non proi</div>
<svg class="abs" style="left:165px;top:3125px" width="18" height="18" viewBox="0 0 18 18"><path d="M3 1l3.5 0 1.3 4-2 1.6c1 2.2 2.6 3.8 4.8 4.8l1.6-2 4 1.3V14c0 1-.8 2-2 2C7 16 2 11 2 3c0-1 .5-2 1-2z" fill="#fff"/></svg>
<div class="ftext" style="left:200px;top:3123px">Phone:<br>+1 555 010 0199</div>
<svg class="abs" style="left:166px;top:3180px" width="18" height="14" viewBox="0 0 18 14"><rect width="18" height="14" rx="1" fill="#fff"/><path d="M1 1l8 7 8-7" stroke="var(--navy-deep)" stroke-width="1.5" fill="none"/></svg>
<div class="ftext" style="left:200px;top:3174px">Email:<br>hello@meadowrunalpacas.example</div>

<div class="ftext" style="left:524px;top:3067px">excepteur sint occaecat cupidatat non<br>&nbsp;proidentsunt in culpa</div>
<div class="abs" style="left:525px;top:3134px;width:252px;height:41px;border-radius:21px;background:#fff;font-size:13px;color:#444;padding:13px 0 0 25px">Enter email</div>
<div class="btn" style="left:525px;top:3190px;width:252px;height:41px;font-size:14px;font-weight:500">SUBSCRIBE</div>

<div class="ftext" style="left:925px;top:3062px;line-height:27.3px">Home<br>About Us<br>Mission<br>Webshop<br>Contact Us</div>

<div class="social" style="left:146px"></div>
<div class="social" style="left:186px"></div>
<div class="social" style="left:226px"></div>
<div class="social" style="left:266px"></div>
<div class="ftext" style="left:640px;width:415px;text-align:right;top:3317px">© 2024 Meadowrun Alpacas. All rights reserved.Privacy Terms of Use</div>

</body>
</html>
```